Norvane Stationery Design Project

We need stationary design that goes with the attached logo. We have logo in two different versions. One in Red/Black and the other in Blue/Green. Red/Black is going to be our primary color and we are planning to use Blue/Green occasionally as necessary.

So we need stationary design in both color combinations. Maybe you can work with Red/Black first and once we decide on the design, then you can show the Blue/Green variation.

Please see the attached png and psd files for logo.

Target Market(s)

IT departments of Medium size Enterprises.

Industry/Entity Type

Work

Requirements
Must have
• -Letter head
-Cover page design for white papers and articles that are going to publish
-Business Card
-Envelope design
Nice to have
• - High level design template that we can follow for our internal web applications

```html
<!DOCTYPE html>
<html lang="en">
<head>
<meta charset="utf-8">
<title>Norvane Software – Business Card</title>
<link href="https://fonts.googleapis.com/css2?family=Lato:wght@400;700;900&display=swap" rel="stylesheet">
<style>
  :root {
    --stage: #2b2b2b;
    --brand-red: #d3141b;
    --brand-red-deep: #a8101a;
    --ink: #111111;
    --paper: #f6f6f6;
    --muted: #e8c9c9;
  }
  * { margin: 0; padding: 0; box-sizing: border-box; }
  html, body { width: 1200px; height: 997px; overflow: hidden; }
  body {
    background: var(--stage);
    font-family: "Lato", Arial, sans-serif;
    position: relative;
  }
  .card {
    position: absolute;
    width: 580px;
    height: 330px;
    border-radius: 3px;
    overflow: hidden;
    box-shadow: 0 18px 40px rgba(0,0,0,.55);
  }
  /* front */
  .card--front {
    left: 90px; top: 110px;
    background: linear-gradient(135deg, #e3161d 0%, var(--brand-red) 55%, var(--brand-red-deep) 100%);
    color: #fff;
  }
  .front-brand {
    position: absolute; left: 110px; top: 110px;
    display: flex; align-items: center; gap: 16px;
  }
  .brand-square { width: 30px; height: 30px; background: currentColor; }
  .brand-name {
    font-weight: 900; font-size: 40px; letter-spacing: 5px; line-height: 1;
    text-transform: uppercase;
  }
  .brand-name small {
    display: block; font-size: 20px; letter-spacing: 12px; margin-top: 8px;
  }
  .front-slogan {
    position: absolute; left: 110px; top: 240px;
    font-size: 14px; letter-spacing: 4px; color: var(--muted);
  }
  /* back */
  .card--back {
    left: 530px; top: 540px;
    background: var(--paper);
    color: var(--ink);
  }
  .back-brand {
    position: absolute; left: 40px; top: 34px;
    display: flex; align-items: center; gap: 14px;
    color: var(--brand-red);
  }
  .back-brand .brand-name { font-size: 38px; }
  .holder { position: absolute; left: 70px; top: 160px; text-align: right; width: 200px; }
  .holder-name { font-size: 24px; letter-spacing: 1px; }
  .holder-role { font-size: 15px; font-weight: 700; color: var(--brand-red); letter-spacing: 1px; }
  .divider {
    position: absolute; left: 290px; top: 132px; width: 2px; height: 110px;
    background: linear-gradient(var(--brand-red), rgba(211,20,27,0));
  }
  .contacts { position: absolute; left: 310px; top: 132px; list-style: none; }
  .contacts li {
    display: flex; align-items: center; gap: 10px;
    font-size: 15px; line-height: 26px;
  }
  .contacts svg { width: 14px; height: 14px; fill: var(--brand-red); flex: none; }
  .address {
    position: absolute; left: 40px; top: 262px;
    font-size: 17px; font-weight: 700; color: var(--brand-red);
  }
  .card-base { position: absolute; left: 0; bottom: 0; width: 580px; height: 60px; }
</style>
</head>
<body>

<section class="card card--front" aria-label="Card front">
  <div class="front-brand">
    <span class="brand-square"></span>
    <div class="brand-name">Norvane<small>Software</small></div>
  </div>
  <p class="front-slogan">YOUR SLOGAN / TAGLINE HERE</p>
</section>

<section class="card card--back" aria-label="Card back">
  <div class="back-brand">
    <span class="brand-square"></span>
    <div class="brand-name">Norvane<small>Software</small></div>
  </div>

  <div class="holder">
    <p class="holder-name">YOUR NAME</p>
    <p class="holder-role">DESIGNATION</p>
  </div>

  <div class="divider"></div>

  <ul class="contacts">
    <li><svg viewBox="0 0 14 14"><path d="M4 0h6a1 1 0 0 1 1 1v12a1 1 0 0 1-1 1H4a1 1 0 0 1-1-1V1a1 1 0 0 1 1-1zm0 2v9h6V2z"/></svg>(555) 014-2288</li>
    <li><svg viewBox="0 0 14 14"><path d="M1 4c0-2 12-2 12 0v1h-3V4H4v1H1zM3 6h8l2 7H1zm4 2a2 2 0 1 0 0 4 2 2 0 0 0 0-4z"/></svg>(555) 017-3340</li>
    <li><svg viewBox="0 0 14 14"><path d="M0 3h14v1L7 8 0 4zm0 2.5l7 4 7-4V11H0z"/></svg>info@norvanesoftware.com</li>
    <li><svg viewBox="0 0 14 14"><path d="M5 9l4-4 1 1-4 4zM3 7l2-2 1 1-2 2a1.4 1.4 0 0 0 2 2l2-2 1 1-2 2a2.8 2.8 0 0 1-4-4zm8 0l-2 2-1-1 2-2a1.4 1.4 0 0 0-2-2L6 6 5 5l2-2a2.8 2.8 0 0 1 4 4z"/></svg>www.norvanesoftware.com</li>
  </ul>

  <p class="address">P.O. Box 118, Larkfield AL, 36990</p>

  <svg class="card-base" viewBox="0 0 580 60" preserveAspectRatio="none" aria-hidden="true">
    <path d="M0 52 L380 52 Q392 52 400 40 L410 26 Q418 16 432 16 L580 16 L580 60 L0 60 Z" fill="#111"/>
    <path d="M398 44 Q408 28 424 24 L580 24 L580 0 L452 0 Q430 0 420 14 Z" fill="var(--brand-red)" transform="translate(0,2)"/>
  </svg>
</section>

</body>
</html>
```